Stock Broking Firm - Web Design Project

We are looking at doing a full re-design of our home page and content page and moving the majority of our content over to DNN.

Phase 1 : Website redesign www.kvtrading.com.au

The current design is too washed out, boring and has no call to action buttons.

Solution:

KV Trading is looking for a brighter/ cleaner redesign with a few stand out call to action buttons.

• Banner with logo across the top horizontally - Bright blue logo on white background similar to www.dlq.com.au - CALL 1300 482 917 - Follow on Chirpline / Friendwall
• Horizontal menu bar - professional looking. - Home - About Us- Our Services - Membership - Open an Account - Become a member - Contact
• Below banner top left - large rotating banner - maybe zumbo gallery style www.tgwhitfields.com.au
• Right of rotating banner - Membership login
• Below members login - Register for Daily Market Report/ research blog - Large bright button / Name / Email / Phone / pop up??
• Below Register for daily market report - Market Indicies - RSS feed of delayed data from QNX see www.tgwhitfields.com
• Below Market indicies - KV TRADING - Market Tweets ( feed from our chirpline page)

Below Rotating Banner -

content area

Below content area - 4 large block buttons see www.harkvine.com.au ( hover over change colour)

Button 1 - EDUCATION - content - click here for more

Button 2 - Market Information and Research

Button 3 - Full service Broker - content brief - click here for more

Button 4 - Trade Commodities and Options

below buttons - small horizontal menu bar slightly different colour incl - Careers/ Partners / Legal Privacy FSG Site Map

Regards,
Owen Pettit

Target Market(s)

35 - 65

Industry/Entity Type

Education

Requirements
Must have
• Follow brief above - large banner, call to action buttons, F.W. Chirpline, Member login etc. 4 big buttons
Nice to have
• clean looking site similar to www.dlq.com.au / not too busy. Corporate looking.
Should not have
• not too busy

```html
<!DOCTYPE html>
<html lang="en">
<head>
<meta charset="utf-8">
<title>KV Trading – Home</title>
<link rel="stylesheet" href="https://fonts.googleapis.com/css2?family=Ubuntu:wght@300;400;500&family=Arimo:wght@400;700&display=swap">
<style>
:root{
  --blue:#1d8fe0;
  --blue-dark:#1a6fc4;
  --navy:#1a3f8f;
  --green:#72b51c;
  --green-dark:#5f9e12;
  --charcoal:#3a3a3a;
  --ink:#333;
  --muted:#666;
  --line:#dcdcdc;
  --page:#efefef;
  --row:#e8f0fb;
  --red:#c0392b;
}
*{box-sizing:border-box;margin:0;padding:0}
html,body{width:1113px;height:1200px;overflow:hidden;background:#fff}
body{font-family:Arimo,Arial,sans-serif;color:var(--ink);position:relative}
.canvas{position:relative;width:1113px;height:1200px;overflow:hidden;background:var(--page)}
.top-zone{position:absolute;left:0;top:0;width:1113px;height:431px;background:#fff}
.header{position:absolute;left:0;top:0;width:1113px;height:50px;background:linear-gradient(#fff,#f1f1f1)}
.brand{position:absolute;left:135px;top:6px;display:flex;align-items:center;gap:8px}
.brand-mark{width:28px;height:28px;background:var(--blue)}
.brand-name{font-family:Ubuntu,sans-serif;font-size:34px;font-weight:400;color:var(--blue);line-height:36px}
.callout{position:absolute;left:656px;top:10px;display:flex;align-items:center;gap:6px}
.callout-icon{width:24px;height:24px;border-radius:50%;background:var(--blue);display:flex;align-items:center;justify-content:center}
.callout-num{font-family:Ubuntu,sans-serif;font-size:25px;font-weight:500;color:#777}
.social{display:flex;gap:4px}
.social span{display:block;width:21px;height:21px;border-radius:50%;background:#fff;border:2px solid #d8e7f5;box-shadow:0 0 2px rgba(0,0,0,.15)}
.header .social{position:absolute;left:860px;top:12px}
.nav{position:absolute;left:0;top:50px;width:1113px;height:48px;background:linear-gradient(#4a4a4a,#2e2e2e)}
.nav a{position:absolute;top:0;height:48px;line-height:48px;color:#fff;text-decoration:none;font-family:Ubuntu,sans-serif;font-size:14.5px}
.nav a.active{background:var(--blue);text-align:center}
.slider{position:absolute;left:117px;top:100px;width:567px;height:325px;box-shadow:0 4px 8px rgba(0,0,0,.25)}
.slider-photo{position:absolute;left:0;top:0;width:567px;height:245px;background:linear-gradient(90deg,#d9d4cf 0%,#e9e5e1 45%,#f4f0ec 70%,#fbfaf8 100%)}
.slider-arrow{position:absolute;top:135px;width:36px;height:36px;border-radius:50%;background:rgba(120,120,120,.35)}
.slider-arrow svg{position:absolute;left:11px;top:10px}
.caption{position:absolute;left:0;top:245px;width:567px;height:80px;background:linear-gradient(#4f4f4f,#3a3a3a)}
.caption h2{position:absolute;left:20px;top:10px;font-family:Ubuntu,sans-serif;font-weight:400;font-size:20px;color:#fff}
.caption p{position:absolute;left:20px;top:38px;width:365px;font-size:10.5px;line-height:12.5px;color:#fff}
.thumbs{position:absolute;left:431px;top:10px;display:grid;grid-template-columns:59px 59px;gap:4px}
.thumbs div{height:29px;border:2px solid #fff}
.login{position:absolute;left:690px;top:100px;width:280px;height:161px;background:linear-gradient(135deg,#80c42a,#67ad16)}
.panel-title{font-family:Ubuntu,sans-serif;font-weight:400;font-size:20px}
.login .panel-title{position:absolute;left:22px;top:14px;color:#fff}
.field-label{position:absolute;left:22px;font-size:11px}
.login .field-label{color:#eaf6d6}
.login .field{position:absolute;left:85px;width:172px;height:26px;background:#4d7d1b;border:1px solid #5f9223}
.forgot{position:absolute;font-size:10.5px;color:#fff;text-decoration:underline}
.btn-blue{position:absolute;display:flex;align-items:center;justify-content:center;background:linear-gradient(#2ea0ee,#1677c9);color:#fff;font-size:11px;font-weight:700;border:1px solid #0f66b0}
.report{position:absolute;left:690px;top:263px;width:280px;height:163px;background:linear-gradient(135deg,#fff 55%,#f0f0f0);border:1px solid var(--line)}
.report .panel-title{position:absolute;left:22px;top:14px;color:var(--navy)}
.report .field-label{color:#333}
.report .field{position:absolute;left:85px;width:172px;height:27px;background:#fff;border:1px solid #c9c9c9;box-shadow:inset 0 1px 2px rgba(0,0,0,.1)}
.card{position:absolute;width:279px;height:270px;background:#fff;border:1px solid var(--line)}
.card-head{height:37px;background:linear-gradient(var(--green),var(--green-dark));color:#fff;font-family:Ubuntu,sans-serif;font-size:19px;line-height:24px;padding:6px 0 0 19px;white-space:nowrap;overflow:hidden}
.card-head.long{font-size:17px;padding-top:7px}
.card-sub{position:absolute;left:19px;top:59px;font-size:11px;font-weight:700;color:#444}
.card-text{position:absolute;left:19px;width:146px;font-size:11px;line-height:16.3px;color:#666}
.card-icon{position:absolute;top:58px;width:100px;height:100px;border-radius:50%;background:var(--charcoal);display:flex;align-items:center;justify-content:center}
.read-more{position:absolute;left:19px;bottom:13px;width:241px;height:26px;display:flex}
.read-more span{flex:1;background:linear-gradient(#f0f0f0,#c8c8c8);font-family:Ubuntu,sans-serif;font-size:13px;line-height:26px;padding-left:17px;color:#333}
.read-more i{width:56px;background:linear-gradient(90deg,#1d6fd0 0 55%,#2a84e0 55%);display:flex;align-items:center;justify-content:flex-end;padding-right:9px}
.side-box{position:absolute;left:690px;width:280px;background:#fff;border:1px solid var(--line)}
.side-head{height:37px;display:flex;align-items:center;gap:12px;padding-left:10px;font-family:Ubuntu,sans-serif;font-size:19.5px;color:#fff}
.side-head .dot{width:24px;height:24px;border-radius:50%;background:#fff;display:flex;align-items:center;justify-content:center}
.head-dark{background:linear-gradient(#5a5a5a,#333)}
.head-blue{background:linear-gradient(#2a9cec,#1678cb)}
.quotes{position:absolute;left:5px;top:47px;width:268px;border-collapse:collapse;font-size:9.5px}
.quotes th{text-align:left;font-weight:700;color:#222;height:22px;padding-left:5px}
.quotes td{height:21px;padding-left:3px;color:#333;border-bottom:1px solid #fff}
.quotes tr:nth-child(odd) td{background:var(--row)}
.quotes td.neg{color:var(--red)}
.post{position:absolute;left:14px;width:253px;font-size:10px;color:#555}
.post h3{font-size:10.5px;font-weight:700;color:#333;width:180px;line-height:12px}
.post time{position:absolute;right:0;top:0;font-size:10.5px;color:#555}
.post p{margin-top:8px;line-height:12.5px}
.post-rule{position:absolute;left:14px;width:253px;border-top:1px dashed #aaa}
.tweet{position:absolute;left:14px;width:250px;height:48px;background:#f4f4f4;border-bottom:1px solid #fff}
.avatar{position:absolute;left:8px;top:9px;width:34px;height:34px}
.tweet .who{position:absolute;left:50px;top:8px;font-family:Ubuntu,sans-serif;font-size:11px;color:var(--blue)}
.tweet .where{position:absolute;left:50px;top:25px;font-family:Ubuntu,sans-serif;font-size:11px;color:#333}
.tweet .where b{font-weight:400;color:var(--blue);margin-left:4px}
.partners{position:absolute;left:117px;top:990px;width:567px;height:133px;background:#fff;border:1px solid var(--line)}
.partners .side-head{padding-left:20px}
.badges{position:absolute;left:17px;top:70px;display:flex;gap:22px;align-items:center}
.badges span{display:block;height:20px;border-radius:3px}
.footer{position:absolute;left:0;top:1148px;width:1113px;height:52px;background:var(--blue);color:#fff;font-size:10.5px}
.footer-links{position:absolute;left:114px;top:19px}
.footer-links a{color:#fff;text-decoration:none}
.footer-links em{font-style:normal;margin:0 6px}
.footer .social{position:absolute;left:475px;top:14px}
.footer .social span{border-color:#cfe6f8}
.copyright{position:absolute;right:150px;top:19px;left:auto;width:auto}
</style>
</head>
<body>
<div class="canvas">
  <div class="top-zone"></div>

  <header class="header">
    <div class="brand"><span class="brand-mark"></span><span class="brand-name">KV Trading</span></div>
    <div class="callout">
      <span class="callout-icon"><svg width="13" height="13" viewBox="0 0 24 24"><path fill="#fff" d="M6.6 10.8a15.1 15.1 0 0 0 6.6 6.6l2.2-2.2a1 1 0 0 1 1-.25 11.4 11.4 0 0 0 3.6.57 1 1 0 0 1 1 1V20a1 1 0 0 1-1 1A17 17 0 0 1 3 4a1 1 0 0 1 1-1h3.5a1 1 0 0 1 1 1c0 1.25.2 2.45.57 3.57a1 1 0 0 1-.25 1z"/></svg></span>
      <span class="callout-num">1300 482 917</span>
    </div>
    <div class="social" aria-label="Social links"><span></span><span></span><span></span><span></span></div>
  </header>

  <nav class="nav">
    <a href="#" style="left:138px">Home</a>
    <a href="#" style="left:221px">About Us</a>
    <a href="#" style="left:317px">Our Services</a>
    <a href="#" class="active" style="left:413px;width:121px">Membership</a>
    <a href="#" style="left:555px">Open an Account</a>
    <a href="#" style="left:715px">Become a member</a>
    <a href="#" style="left:885px">Contact</a>
  </nav>

  <section class="slider">
    <div class="slider-photo" role="img" aria-label="Banner photo of a smiling businesswoman in front of a group of colleagues"></div>
    <span class="slider-arrow" style="left:7px"><svg width="14" height="16"><path d="M10 2 4 8l6 6" fill="none" stroke="#fff" stroke-width="2"/></svg></span>
    <span class="slider-arrow" style="left:526px"><svg width="14" height="16"><path d="M4 2l6 6-6 6" fill="none" stroke="#fff" stroke-width="2"/></svg></span>
    <div class="caption">
      <h2>HIGHER POTENTIAL RETURN</h2>
      <p>Trading options on Australian stocks or commodities such as gold and silver, you spend much less money and make almost the same profit as if you buy or sell Australian stocks.</p>
      <div class="thumbs">
        <div role="img" aria-label="Thumbnail: business team" style="background:#d8d0c8"></div>
        <div role="img" aria-label="Thumbnail: people on a chart" style="background:#e4e4e4"></div>
        <div role="img" aria-label="Thumbnail: world map" style="background:#b9bcbf"></div>
        <div role="img" aria-label="Thumbnail: rising graph" style="background:#f2f2f2"></div>
      </div>
    </div>
  </section>

  <section class="login">
    <h2 class="panel-title">Members Login</h2>
    <span class="field-label" style="top:58px">Username</span>
    <span class="field" style="top:51px"></span>
    <span class="field-label" style="top:90px">Password</span>
    <span class="field" style="top:83px"></span>
    <a class="forgot" href="#" style="left:94px;top:121px">Forget password?</a>
    <span class="btn-blue" style="left:195px;top:114px;width:62px;height:25px">Login</span>
  </section>

  <section class="report">
    <h2 class="panel-title">Daily Market Report</h2>
    <span class="field-label" style="top:60px">Name</span>
    <span class="field" style="top:49px"></span>
    <span class="field-label" style="top:94px">Email</span>
    <span class="field" style="top:83px"></span>
    <span class="btn-blue" style="left:165px;top:116px;width:92px;height:27px">Register</span>
  </section>

  <article class="card" style="left:117px;top:437px">
    <div class="card-head">Education</div>
    <p class="card-sub" style="top:56px">Get Education info from here</p>
    <p class="card-text" style="top:78px">Lorem ipsum dolor sit amet, consectetuer adipiscing elit, sed diam nonummy nibh euismod tincidunt ut laoreet dolore magna aliqlobortis nisl ut aliquip ex ea commodo consequat.</p>
    <div class="card-icon" style="left:164px;top:56px"><svg width="52" height="34" viewBox="0 0 52 34" fill="#fff"><circle cx="14" cy="9" r="6"/><circle cx="38" cy="9" r="6"/><circle cx="26" cy="7" r="7"/><path d="M2 30c0-8 5-12 12-12s12 4 12 12z"/><path d="M26 30c0-8 5-12 12-12s12 4 12 12z"/><path d="M12 32c0-9 6-14 14-14s14 5 14 14z"/></svg></div>
    <div class="read-more"><span>Read More</span><i><svg width="9" height="14"><path d="M1 1l6 6-6 6" fill="none" stroke="#fff" stroke-width="1.6"/></svg></i></div>
  </article>

  <article class="card" style="left:406px;top:437px">
    <div class="card-head">Market Info and Research</div>
    <p class="card-sub" style="top:56px">Get Market info from here</p>
    <p class="card-text" style="top:84px">Lorem ipsum dolor sit amet, consectetuer adipiscing elit, sed diam nonummy nibh euismod tincidunt ut laoreet dolore magna aliqlobortis nisl ut aliquip ex ea commodo consequat.</p>
    <div class="card-icon" style="left:168px;top:56px"><svg width="50" height="36" viewBox="0 0 50 36"><rect x="7" y="3" width="36" height="24" rx="2" fill="none" stroke="#fff" stroke-width="4"/><path d="M1 30h48v3H1z" fill="#fff"/></svg></div>
    <div class="read-more"><span>Read More</span><i><svg width="9" height="14"><path d="M1 1l6 6-6 6" fill="none" stroke="#fff" stroke-width="1.6"/></svg></i></div>
  </article>

  <article class="card" style="left:117px;top:712px">
    <div class="card-head">Full Service Broker</div>
    <p class="card-sub" style="top:56px">Get Education info from here</p>
    <p class="card-text" style="top:82px">Lorem ipsum dolor sit amet, consectetuer adipiscing elit, sed diam nonummy nibh euismod tincidunt ut laoreet dolore magna aliqlobortis nisl ut aliquip ex ea commodo consequat.</p>
    <div class="card-icon" style="left:160px;top:53px"><svg width="44" height="44" viewBox="0 0 44 44"><circle cx="22" cy="22" r="18" fill="none" stroke="#fff" stroke-width="4"/><path d="M22 10v14" stroke="#fff" stroke-width="4"/><circle cx="22" cy="25" r="3" fill="#fff"/></svg></div>
    <div class="read-more"><span>Read More</span><i><svg width="9" height="14"><path d="M1 1l6 6-6 6" fill="none" stroke="#fff" stroke-width="1.6"/></svg></i></div>
  </article>

  <article class="card" style="left:406px;top:712px">
    <div class="card-head long">Trade Commodities and Options</div>
    <p class="card-sub" style="top:56px">Get Market info from here</p>
    <p class="card-text" style="top:82px">Lorem ipsum dolor sit amet, consectetuer adipiscing elit, sed diam nonummy nibh euismod tincidunt ut laoreet dolore magna aliqlobortis nisl ut aliquip ex ea commodo consequat.</p>
    <div class="card-icon" style="left:168px;top:53px"><svg width="42" height="42" viewBox="0 0 42 42"><g stroke="#fff" stroke-width="7"><path d="M21 3v36M3 21h36M8 8l26 26M34 8 8 34"/></g><circle cx="21" cy="21" r="13" fill="#fff"/><circle cx="21" cy="21" r="6" fill="#3a3a3a"/></svg></div>
    <div class="read-more"><span>Read More</span><i><svg width="9" height="14"><path d="M1 1l6 6-6 6" fill="none" stroke="#fff" stroke-width="1.6"/></svg></i></div>
  </article>

  <section class="side-box" style="top:437px;height:182px">
    <div class="side-head head-dark"><span class="dot"></span>Market Report</div>
    <table class="quotes">
      <tr><th>Name</th><th>Value</th><th>+/-</th><th>%+/-</th></tr>
      <tr><td>All Shares</td><td>4,511.90</td><td class="neg">-14.70</td><td class="neg">-0.32</td></tr>
      <tr><td>AUX200</td><td>4,490.74</td><td class="neg">-14.56</td><td class="neg">-0.32</td></tr>
      <tr><td>DWL</td><td>13,473.53</td><td class="neg">-110.12</td><td class="neg">-0.81</td></tr>
      <tr><td>HKIdx</td><td>20,919.60</td><td class="neg">-17.68</td><td class="neg">-0.08</td></tr>
      <tr><td>NXQ</td><td>3,065.02</td><td class="neg">-47.33</td><td class="neg">-1.52</td></tr>
    </table>
  </section>

  <section class="side-box" style="top:630px;height:287px">
    <div class="side-head head-blue"><span class="dot"></span>Research Blog</div>
    <div class="post" style="top:49px">
      <h3>$A down after GFB lowers growth forecasts</h3><time>04:46 PM</time>
      <p>Lorem ipsum dolor sit amet, consectetuer adipiscing elit, sed diam nonummy nibh euismod tincidunt ut laoreet dolore magna aliqlobortis nisl ut aliquip ex ea commodo consequat.</p>
    </div>
    <div class="post-rule" style="top:147px"></div>
    <div class="post" style="top:164px">
      <h3>$A down after GFB lowers growth forecasts</h3><time>04:23 PM</time>
      <p>Lorem ipsum dolor sit amet, consectetuer adipiscing elit, sed diam nonummy nibh euismod tincidunt ut laoreet dolore magna aliquam erat volutpat. Ut wisi enim ad minim veniam, quis nostrud exerci tation ullamcorper suscipit lobortis nisl ut aliquip ex ea commodo consequat.</p>
    </div>
  </section>

  <section class="side-box" style="top:922px;height:206px">
    <div class="side-head head-dark"><span class="dot"></span>Chirpline feeds</div>
    <div class="tweet" style="top:42px"><span class="avatar" role="img" aria-label="User avatar" style="background:#e9e2da"></span><span class="who">helen2012</span><span class="where">Posted on<b>Four Quiet Chairs</b></span></div>
    <div class="tweet" style="top:91px"><span class="avatar" role="img" aria-label="User avatar" style="background:#9a8f86"></span><span class="who">Super User</span><span class="where">Posted on<b>Riverside Fans Club</b></span></div>
    <div class="tweet" style="top:140px"><span class="avatar" role="img" aria-label="User avatar" style="background:#b4a59b"></span><span class="who">Marco Delvi</span><span class="where">Posted on<b>Four Quiet Chairs</b></span></div>
  </section>

  <section class="partners">
    <div class="side-head head-dark">Partners</div>
    <div class="badges" aria-label="Partner badges">
      <span style="width:70px;background:#d33"></span>
      <span style="width:62px;background:#c9a24a"></span>
      <span style="width:72px;background:#e36a7a"></span>
      <span style="width:70px;background:#2f8f7f"></span>
      <span style="width:40px;height:36px;border-radius:50%;background:#1b6fbf"></span>
      <span style="width:58px;background:#c6284a"></span>
    </div>
  </section>

  <footer class="footer">
    <div class="footer-links"><a href="#">Careers</a><em>|</em><a href="#">Partners</a><em>|</em><a href="#">Legal Privacy</a><em>|</em><a href="#">FSG Site Map</a></div>
    <div class="social" aria-label="Social links"><span></span><span></span><span></span><span></span></div>
    <div class="footer-links copyright">© 2012 KV Trading (QLD) Pty Ltd, All Rights Reserved.</div>
  </footer>
</div>
</body>
</html>
```